Business card for Luxury Portable Restroom Trailer company

We are a Luxury Portable Restroom Trailer Company Called FALCRIDGE HIRES. Based in Orange County California. We provide portable restroom trailers for events, such as, Weddings, Concerts, Charity events, Sporting events, Tournaments, Corporate events, ect. We rent and Sell the Luxury restrooms. Our colors are white, grey, and Orange. As you will see in the logo we uploaded.
There are 2 people in the company so the names and titles will change for the 3 people but card will remain the same. Here is the information for each Person: Dwight Penner CFO 555 318-0476
next Person: Leon Marchetti VP 555 318-0476
Next Person: Owen Marchetti CEO 555 318-0476
Information to include on the card: Luxury Restroom Trailers Rental and Sales. Weddings, Concerts, Charity, Sporting and Corp. Events.

```html
<!DOCTYPE html>
<html lang="en">
<head>
<meta charset="utf-8">
<title>Falcridge Hires – Business Card</title>
<link rel="stylesheet" href="https://fonts.googleapis.com/css2?family=Montserrat:wght@400;500;600;700;800&display=swap">
<style>
  :root {
    --orange: #e8601f;
    --orange-light: #f0772e;
    --orange-deep: #de5518;
    --grey-dark: #4a4a4c;
    --grey-line: #8a8a8c;
    --grey-bg: #bdbdbd;
    --white: #ffffff;
    --ink: #3a3a3c;
  }
  * { box-sizing: border-box; margin: 0; padding: 0; }
  html, body {
    width: 1200px; height: 802px; overflow: hidden;
    background: var(--grey-bg);
    font-family: "Montserrat", sans-serif;
  }
  .canvas {
    position: relative; width: 1200px; height: 802px;
    display: flex; align-items: center; justify-content: center; gap: 40px;
  }
  .card {
    position: relative; width: 540px; height: 309px;
    border-radius: 22px; overflow: hidden;
    box-shadow: 0 14px 28px rgba(0,0,0,0.22);
  }

  /* Front */
  .card--front { background: var(--white); }
  .brand {
    position: absolute; display: flex; align-items: center; gap: 10px;
    font-weight: 800; letter-spacing: 1px; white-space: nowrap;
  }
  .card--front .brand { top: 40px; right: 44px; color: var(--orange); font-size: 24px; }
  .brand__square { width: 16px; height: 16px; background: currentColor; flex: none; }
  .divider {
    position: absolute; left: 40px; right: 64px; top: 168px;
    height: 1px; background: var(--grey-line);
  }
  .person { position: absolute; left: 40px; top: 112px; }
  .person__name { color: var(--orange); font-weight: 700; font-size: 24px; line-height: 1.1; }
  .person__title { color: var(--ink); font-weight: 500; font-size: 14px; margin-top: 4px; letter-spacing: 0.5px; }
  .contacts { position: absolute; left: 40px; top: 184px; list-style: none; }
  .contacts li {
    display: flex; align-items: center; gap: 9px;
    color: var(--ink); font-size: 14px; font-weight: 500; line-height: 24px;
  }
  .contacts svg { width: 13px; height: 13px; flex: none; }
  .footer-band { position: absolute; left: 0; bottom: 0; width: 540px; height: 40px; }

  /* Back */
  .card--back {
    background: linear-gradient(135deg, var(--orange-light), var(--orange-deep));
  }
  .card--back .decor {
    position: absolute; right: -40px; top: -30px; width: 360px; height: 320px;
    border-radius: 50%;
    background: radial-gradient(circle, rgba(255,255,255,0.08), rgba(255,255,255,0) 70%);
  }
  .card--back .brand-frame {
    position: absolute; left: 50%; top: 74px; transform: translateX(-50%);
    border: 4px solid var(--white); padding: 18px 26px;
  }
  .card--back .brand {
    position: static; color: var(--white); font-size: 34px;
  }
  .brand__square--lg { width: 22px; height: 22px; }
  .tagline {
    position: absolute; left: 0; right: 0; top: 210px;
    text-align: center; color: var(--white); font-weight: 600; line-height: 1.55;
  }
  .tagline__main { font-size: 15px; letter-spacing: 0.3px; }
  .tagline__events { font-size: 15px; font-weight: 500; }
</style>
</head>
<body>
<main class="canvas">

  <section class="card card--front" aria-label="Business card front">
    <div class="brand"><span class="brand__square"></span>FALCRIDGE HIRES</div>

    <div class="person">
      <p class="person__name">Owen Marchetti</p>
      <p class="person__title">CEO</p>
    </div>

    <div class="divider"></div>

    <ul class="contacts">
      <li>
        <svg viewBox="0 0 16 16" aria-hidden="true"><path fill="#e8601f" d="M3.6 1.5l2.2 2.6-1.3 1.6a9 9 0 0 0 5.8 5.8l1.6-1.3 2.6 2.2-1.3 2.1C7 14.2 1.8 9 1.5 2.8z"/></svg>
        555 318-0476
      </li>
      <li>
        <svg viewBox="0 0 16 16" aria-hidden="true"><rect x="1" y="3" width="14" height="10" rx="1.5" fill="#e8601f"/><path d="M2 4l6 5 6-5" fill="none" stroke="#fff" stroke-width="1.4"/></svg>
        owen@falcridgehires.com
      </li>
      <li>
        <svg viewBox="0 0 16 16" aria-hidden="true"><circle cx="8" cy="8" r="7" fill="#e8601f"/><path d="M1.5 8h13M8 1.2c-3 3.5-3 10 0 13.6M8 1.2c3 3.5 3 10 0 13.6" fill="none" stroke="#fff" stroke-width="1"/></svg>
        www.falcridgehires.com
      </li>
    </ul>

    <svg class="footer-band" viewBox="0 0 540 40" preserveAspectRatio="none" aria-hidden="true">
      <polygon points="300,40 336,0 540,0 540,40" fill="#4a4a4c"/>
      <polygon points="0,40 20,26 340,26 330,40" fill="#e8601f"/>
      <polygon points="318,40 346,10 540,10 540,40" fill="#e8601f"/>
    </svg>
  </section>

  <section class="card card--back" aria-label="Business card back">
    <div class="decor" role="img" aria-label="Faint oversized brand decoration"></div>
    <div class="brand-frame">
      <div class="brand"><span class="brand__square brand__square--lg"></span>FALCRIDGE HIRES</div>
    </div>
    <div class="tagline">
      <p class="tagline__main">Luxury Restroom Trailers Rental and Sales</p>
      <p class="tagline__events">Weddings | Concerts | Charity | Sporting | Corp</p>
    </div>
  </section>

</main>
</body>
</html>
```